Business Card Design

New business card design

Target Market(s)

Residential & Commercial Property Managers

Industry/Entity Type

Plumbing Services

Contact Information for Business Card

Name - Rowan Keddle, title - Director, Phone Number - 0431 286 517, email - rowan@tbk-plumbing.com.au, Company ABN - 73 215 904 386,

Font styles to use
Sans Serif

Colors
0054AA
0677BA
7BADD7
CADEEF
E8F1F8

```html
<!DOCTYPE html>
<html lang="en">
<head>
<meta charset="utf-8">
<title>TBK Plumbing – Business Card</title>
<link href="https://fonts.googleapis.com/css2?family=Poppins:wght@400;500;600;700&display=swap" rel="stylesheet">
<style>
  :root {
    --stage: #9a9a9a;
    --paper: #ffffff;
    --paper-tint: #f3f4f5;
    --navy: #0f4a6b;
    --ink: #13202b;
    --title-ink: #0d3d5f;
    --body-ink: #2a2a2a;
    --sky: #00aeef;
    --sky-edge: #1a9ad9;
  }
  * { margin: 0; padding: 0; box-sizing: border-box; }
  html, body { width: 1200px; height: 1108px; overflow: hidden; }
  body { background: var(--stage); font-family: "Poppins", sans-serif; position: relative; }

  .card {
    position: absolute; top: 124px; width: 491px; height: 860px;
    background: var(--paper); overflow: hidden;
    box-shadow: 0 4px 14px rgba(0,0,0,.35);
  }
  .card--front { left: 84px; }
  .card--back { left: 625px; }
  .card svg.card__art { position: absolute; inset: 0; width: 100%; height: 100%; }

  .brand { position: absolute; left: 0; width: 100%; text-align: center; }
  .brand__name {
    display: inline-flex; align-items: center; gap: 14px;
    font-weight: 600; color: var(--ink); letter-spacing: 1px;
  }
  .brand__dot { border-radius: 50%; background: var(--sky); display: inline-block; }
  .card--front .brand { top: 196px; }
  .card--front .brand__name { font-size: 56px; }
  .card--front .brand__dot { width: 26px; height: 26px; }
  .card--back .brand { top: 128px; }
  .card--back .brand__name { font-size: 52px; }
  .card--back .brand__dot { width: 24px; height: 24px; }

  .person { position: absolute; left: 71px; top: 328px; }
  .person__name { font-weight: 700; font-size: 40px; color: var(--title-ink); line-height: 1.2; }
  .person__role { font-weight: 500; font-size: 27px; letter-spacing: 3px; color: var(--body-ink); margin-top: 2px; }

  .contact { position: absolute; left: 75px; top: 446px; list-style: none; }
  .contact__item { display: flex; align-items: center; gap: 10px; height: 40px; font-size: 24px; color: var(--body-ink); }
  .contact__icon { width: 30px; height: 30px; flex: none; }

  .abn { position: absolute; left: 0; width: 100%; top: 714px; text-align: center; font-size: 28px; font-weight: 500; color: var(--paper); }
  .abn__label { color: var(--sky); }
</style>
</head>
<body>

<section class="card card--front">
  <svg class="card__art" viewBox="0 0 491 860" aria-hidden="false">
    <rect role="img" aria-label="Faint pipework pattern in light grey" x="0" y="0" width="491" height="620" fill="var(--paper-tint)" opacity=".55"/>
    <path d="M0,604 C110,572 250,577 370,590 C448,552 482,472 491,368 V860 H0Z" fill="var(--sky-edge)"/>
    <path role="img" aria-label="Dark navy pipework pattern" d="M0,612 C110,580 250,585 370,598 C450,560 486,480 491,376 V860 H0Z" fill="var(--navy)"/>
    <circle cx="252" cy="636" r="126" fill="var(--paper)"/>
    <circle cx="252" cy="636" r="120" fill="var(--sky)"/>
  </svg>
  <div class="brand"><span class="brand__name"><span class="brand__dot"></span>TBK Plumbing</span></div>
</section>

<section class="card card--back">
  <svg class="card__art" viewBox="0 0 491 860">
    <rect role="img" aria-label="Faint pipework pattern in light grey" x="0" y="0" width="491" height="545" fill="var(--paper-tint)" opacity=".55"/>
    <path d="M0,500 C20,592 80,632 180,626 C280,620 380,592 491,642 V860 H0Z" fill="var(--sky-edge)"/>
    <path role="img" aria-label="Dark navy pipework pattern" d="M0,508 C20,600 80,640 180,634 C280,628 380,600 491,650 V860 H0Z" fill="var(--navy)"/>
  </svg>

  <div class="brand"><span class="brand__name"><span class="brand__dot"></span>TBK Plumbing</span></div>

  <div class="person">
    <h1 class="person__name">Rowan Keddle</h1>
    <p class="person__role">DIRECTOR</p>
  </div>

  <ul class="contact">
    <li class="contact__item">
      <svg class="contact__icon" viewBox="0 0 30 30"><circle cx="15" cy="15" r="15" fill="var(--sky-edge)"/><path d="M10.5 8.5l3 3-1.6 1.8c.9 1.9 2.4 3.4 4.3 4.3l1.8-1.6 3 3-1.8 2c-5.5-.6-9.9-5-10.5-10.5z" fill="#fff"/></svg>
      <span>0431 286 517</span>
    </li>
    <li class="contact__item">
      <svg class="contact__icon" viewBox="0 0 30 30"><circle cx="15" cy="15" r="15" fill="var(--sky-edge)"/><rect x="8" y="10" width="14" height="10" rx="1" fill="#fff"/><path d="M8.5 10.5l6.5 5 6.5-5" fill="none" stroke="var(--sky-edge)" stroke-width="1.4"/></svg>
      <span>rowan@tbk-plumbing.com.au</span>
    </li>
  </ul>

  <p class="abn"><span class="abn__label">ABN</span> - 73 215 904 386</p>
</section>

</body>
</html>
```